WTF!!! We need a modern professional website for a business litigation law firm.

We need a modern, clean, professional and uncomplicated website for a new business trial and litigation law firm called "Haverlock Trial Firm PLLC". Website must be mobile optimized for iPad and smartphone. The law firm specializes in counseling and representing large corporations, small businesses and entrepreneurs in and out of the courtroom. Lawyers in the firm serve as Florida counsel and trial counsel to organizations facing claims involving product liability, premises liability, professional liability, vehicle and transportation liability, warranty claims, construction defects and delay claims, complex business disputes, commercial litigation and bid disputes in State and Federal Courts. The website is mainly to provide information about the firm, and should include sections describing the firm, identifying the Industries Served and Areas of Practice ," a separate page identifying the "Professionals", a separate page for "Resources & Advisories," and a traveling "Connect With Us" button a site visitor can click on that will launch an email to the Firm's general email account. The website should allow us to easily modify the content on these pages, and let us add/modify links to external information sources. We will not sell anything or take payments through the website. We do need to be able to easily upload and update photographs of attorneys and add new attorneys names/email hyperlinks as the firm grows. We would like to add developments in the law or success stories easily and quickly, such as through a blog page. On the "Connect With Us" page the website should have hyperlinks to email the Firm, and there should be hyperlinks to email each professional on the "Professionals" page. The website should be viewable on mobile devices without distortion. The law firm focuses on trial work and should have some imagery associated with courtrooms, but the overall theme of the site should be modern, clean, and communicate sophistication and strength. The website should be made in Wordpress. We have uploaded logo files for Haverlock Trial Firm.

Target Market(s)

Corporations and companies that are looking for legal representation. Other attorneys/legal industry.

Industry/Entity Type

Legal Industry

Coding

Coded - Design and coding required

Number of Pages Required

1 page

Font styles to use
Sans Serif

Requirements
Must have
• Simple, clean, sophisticated, modern website that includes the logo, watermark of logo, and the elements described above.
Nice to have
• Pictures of city scape, buildings, courtroom, team members.

```html
<!DOCTYPE html>
<html lang="en">
<head>
<meta charset="utf-8">
<title>Haverlock Trial Firm — Business Litigation</title>
<link href="https://fonts.googleapis.com/css2?family=Montserrat:wght@400;500;600;700;800&family=Libre+Baskerville:wght@700&display=swap" rel="stylesheet">
<style>
:root{
  --blue:#1877e0;
  --blue-dark:#0f63c4;
  --gold:#c98f4c;
  --ink:#151515;
  --text:#333;
  --muted:#555;
  --gray-bg:#f2f2f2;
  --white:#fff;
}
*{box-sizing:border-box;margin:0;padding:0}
html,body{width:1200px;height:4946px;overflow:hidden}
body{font-family:'Montserrat',sans-serif;color:var(--text);background:var(--white);position:relative}
.abs{position:absolute}
.eyebrow{color:var(--blue);font-size:16px;font-weight:500;letter-spacing:.5px;text-transform:uppercase}
.section-title{color:var(--ink);font-size:31px;font-weight:800;letter-spacing:.5px;text-transform:uppercase}
.center{text-align:center;left:0;width:1200px}
.btn-blue{background:var(--blue);color:#fff;font-size:12px;font-weight:600;letter-spacing:1px;text-transform:uppercase;display:flex;align-items:center;justify-content:center}
.btn-blue::after{content:"";position:absolute;left:18px;right:18px;bottom:-7px;height:2px;background:var(--blue)}

/* hero */
.hero{left:0;top:0;width:1200px;height:601px;background:linear-gradient(90deg,#1b130e 0%,#3a2a20 45%,#4a3628 70%,#2b1e16 100%)}
.hero-shade{left:0;top:0;width:1200px;height:601px;background:linear-gradient(180deg,rgba(0,0,0,.45) 0%,rgba(0,0,0,.1) 40%,rgba(0,0,0,.5) 100%)}
.brand{left:140px;top:20px;color:#fff;font-weight:700;font-size:15px;line-height:1.1;letter-spacing:.5px;display:flex;align-items:center;gap:8px}
.brand-dot{width:14px;height:14px;background:#fff;border-radius:50%}
.nav{left:374px;top:33px;display:flex;gap:36px;color:#fff;font-size:12px}
.nav .active{font-weight:700}
.nav-contact{left:960px;top:26px;width:98px;height:33px;border-radius:17px;background:var(--gold);color:#fff;font-size:12px;font-weight:600;display:flex;align-items:center;justify-content:center}
.hero-title{left:140px;top:228px;color:#fff;font-family:'Libre Baskerville',serif;font-size:43px;line-height:58px}
.hero-sub{left:140px;top:357px;color:#fff;font-size:14px;letter-spacing:.3px}
.hero-btn{left:140px;top:405px;width:127px;height:37px;border-radius:19px;background:var(--gold);color:#fff;font-size:12px;font-weight:600;display:flex;align-items:center;justify-content:center}
.connect-tab{left:1165px;top:275px;width:35px;height:138px;background:var(--gold);color:#fff;font-size:11px;font-weight:700;display:flex;align-items:center;justify-content:center}
.connect-tab span{transform:rotate(-90deg);white-space:nowrap}
.scroll-notch{left:530px;top:600px;width:140px;height:12px;background:var(--blue);clip-path:polygon(0 0,100% 0,75% 100%,25% 100%)}
.scroll-circle{left:560px;top:576px;width:80px;height:80px;border-radius:50%;background:#fff;display:flex;align-items:center;justify-content:center}

/* about */
.about-media{left:144px;top:762px;width:501px;height:277px;background:linear-gradient(135deg,#6b6f78 0%,#a8a49b 40%,#7a5a46 70%,#3e4452 100%)}
.about-text{left:693px;top:734px;width:370px}
.about-text h2{font-size:30px;font-weight:800;color:var(--ink);margin-top:6px;letter-spacing:.5px}
.about-text h3{font-size:15px;font-weight:600;color:var(--ink);letter-spacing:1px;margin-top:2px}
.about-text p{font-size:12.5px;line-height:22px;color:var(--text);margin-top:12px}
.about-btn{left:693px;top:1014px;width:139px;height:44px}

/* practice */
.practice{left:0;top:1158px;width:1200px;height:1040px;background:var(--gray-bg)}
.card{width:294px;height:328px;overflow:hidden}
.card-photo{position:absolute;inset:0}
.card-shade{position:absolute;inset:0;background:linear-gradient(180deg,rgba(0,0,0,0) 45%,rgba(0,0,0,.75) 100%)}
.card-label{position:absolute;left:20px;right:20px;bottom:28px;color:#fff;font-size:16px;font-weight:700;letter-spacing:.3px;display:flex;justify-content:space-between;align-items:center}
.card-open{background:#1d1d1f;border:2px solid var(--blue);padding:54px 26px 0}
.card-open h4{color:#fff;font-size:16px;font-weight:700;letter-spacing:.3px}
.card-open p{color:#ddd;font-size:12px;line-height:22px;margin-top:14px}
.card-open a{display:block;color:var(--blue);font-size:11px;font-weight:600;margin-top:26px;text-decoration:none}

/* industries */
.ind-card{width:294px;height:307px;background:#fff;box-shadow:0 6px 24px rgba(0,0,0,.09);text-align:center;padding-top:38px}
.ind-card h4{font-size:18px;font-weight:700;color:var(--ink);margin-top:14px;letter-spacing:.5px}
.ind-card p{font-size:12px;line-height:22px;color:var(--muted);margin:12px 30px 0}
.ind-card .arrow{margin-top:20px}

/* cta */
.cta{left:0;top:2784px;width:1200px;height:461px;background:linear-gradient(120deg,#2a2c30 0%,#3e3b37 45%,#23252a 100%)}
.cta-shade{left:0;top:2784px;width:1200px;height:461px;background:rgba(0,0,0,.35)}
.cta-title{top:2880px;color:#fff;font-size:40px;font-weight:800;line-height:50px;letter-spacing:.5px}
.cta-text{top:2995px;color:#fff;font-size:17px;line-height:29px}
.cta-btn{left:506px;top:3083px;width:188px;height:45px}

/* blog */
.blog-photo{left:140px;top:3429px;width:447px;height:282px;background:linear-gradient(135deg,#5d7d92 0%,#a7b4ba 45%,#7b5a4b 100%)}
.meta{font-size:13px;color:var(--ink);letter-spacing:.3px}
.post-title{font-size:15px;font-weight:700;color:var(--ink);line-height:23px}
.learn{font-size:11px;font-weight:600;color:var(--blue);letter-spacing:.5px}
.post-side{left:626px;width:200px}
.thumb{left:847px;width:211px;height:134px}

/* testimonials */
.reviews{left:0;top:4051px;width:1200px;height:519px;background:var(--gray-bg)}
.avatar{width:30px;height:30px;border-radius:50%;border:2px solid #fff;position:absolute;top:0}
.quote-card-back{left:530px;top:4197px;width:528px;height:259px;background:#fff;opacity:.6}
.quote-card{left:553px;top:4170px;width:482px;height:304px;background:#fff;box-shadow:0 6px 24px rgba(0,0,0,.08)}
.quote-icon{left:592px;top:4146px;width:50px;height:50px;border-radius:50%;background:var(--blue);display:flex;align-items:center;justify-content:center;color:#fff;font-family:'Libre Baskerville',serif;font-size:34px;line-height:1}
.slider-btn{width:24px;height:24px;border-radius:50%;display:flex;align-items:center;justify-content:center}

/* footer */
.footer{left:0;top:4570px;width:1200px;height:376px;background:var(--blue)}
.foot-h{color:#fff;font-size:15px;font-weight:700;letter-spacing:1px;top:4634px}
.foot-list{color:#fff;font-size:12.5px;line-height:27px;list-style:none}
.foot-list li::before{content:"· "}
.contact-item{color:#fff;font-size:12.5px;line-height:19px;display:flex;gap:10px}
.contact-item b{font-weight:600;display:block}
.social{color:#fff;font-size:12.5px;display:flex;align-items:center;gap:10px}
.social i{width:28px;height:28px;border:1.5px solid #fff;border-radius:50%;display:block}
.foot-brand{left:858px;top:4690px;width:200px;color:#fff;font-size:34px;font-weight:800;line-height:38px;text-align:center;letter-spacing:1px}
.copyright{top:4912px;color:#fff;font-size:11px}
</style>
</head>
<body>

<!-- hero -->
<section class="abs hero" role="img" aria-label="Young attorney in a dark suit standing in a wood-panelled courtroom"></section>
<div class="abs hero-shade"></div>
<div class="abs brand"><span class="brand-dot"></span><span>HAVERLOCK<br><span style="font-size:9px;letter-spacing:2px">TRIAL FIRM</span></span></div>
<nav class="abs nav"><span class="active">Home</span><span>About Us</span><span>Areas of Practice</span><span>Our Professionals</span><span>Resources &amp; Advisories</span></nav>
<div class="abs nav-contact">Contact Us</div>
<h1 class="abs hero-title">Your Trusted Partner In<br>Business Litigation</h1>
<p class="abs hero-sub">Expert Counsel For Corporations And Entrepreneurs.</p>
<div class="abs hero-btn">Learn More</div>
<div class="abs connect-tab"><span>Connect With Us</span></div>
<div class="abs scroll-notch"></div>
<div class="abs scroll-circle"><svg width="16" height="24" viewBox="0 0 16 24"><rect x="1.5" y="1.5" width="13" height="21" rx="6.5" fill="none" stroke="#1877e0" stroke-width="2"/><line x1="8" y1="6" x2="8" y2="10" stroke="#1877e0" stroke-width="2"/></svg></div>

<!-- about -->
<div class="abs about-media" role="img" aria-label="City skyscrapers with American flags"></div>
<div class="abs about-text">
  <div class="eyebrow">Who We Are</div>
  <h2>ABOUT HAVERLOCK</h2>
  <h3>TRIAL FIRM</h3>
  <p>Lorem ipsum dolor sit amet, consectetuer adipiscing elit sed diam nonummy nibh euismod tincidunt ut.</p>
  <p style="margin-top:10px">Ut wisi enim ad minim veniam, quis nostru ullamcorper suscipit lobortis nisl ut aliquip ex ea commodo conuat. Duis autem vel eum iriure dolor in henrerit in vulputate velit esse molestie conseqat, vel illum dolore eu feugiat nulla facilisis at vero eros et accsan.</p>
</div>
<div class="abs btn-blue about-btn">Learn More</div>

<!-- practice -->
<section class="abs practice"></section>
<div class="abs eyebrow center" style="top:1247px;text-align:center">Who We Serve</div>
<h2 class="abs section-title center" style="top:1272px;text-align:center">Areas of Practice</h2>

<div class="abs card" style="left:140px;top:1342px">
  <div class="card-photo" role="img" aria-label="Businessman signing documents at a desk" style="background:linear-gradient(135deg,#cfcac2,#6e6a66 60%,#2f3440)"></div>
  <div class="card-shade"></div>
  <div class="card-label"><span>PRODUCT LIABILITY</span><span>&rarr;</span></div>
</div>
<div class="abs card card-open" style="left:453px;top:1342px">
  <h4>PROFESSIONAL LIABILITY</h4>
  <p>Ut wisi enim ad inim iam quis nostru ullamcorper suscipit lis nisl ut aliquip ex ea commodo conuat. Duis autem vel eum iriure dolor rerit in vulputate velit esse molestie conseat, vel illum dolore eu feugiat nulla.</p>
  <a>LEARN MORE &rarr;</a>
</div>
<div class="abs card" style="left:765px;top:1342px">
  <div class="card-photo" role="img" aria-label="Premises liability book on a library shelf" style="background:linear-gradient(135deg,#8a6a4a,#3e4c66 55%,#2b2420)"></div>
  <div class="card-shade"></div>
  <div class="card-label"><span>PREMISES LIABILITY</span><span>&rarr;</span></div>
</div>
<div class="abs card" style="left:140px;top:1690px">
  <div class="card-photo" role="img" aria-label="People reviewing a contract with a laptop" style="background:linear-gradient(135deg,#a89a88,#6b6660 55%,#3a3734)"></div>
  <div class="card-shade"></div>
  <div class="card-label"><span>WARRANTY CLAIMS</span><span>&rarr;</span></div>
</div>
<div class="abs card" style="left:453px;top:1690px">
  <div class="card-photo" role="img" aria-label="Handshake over a desk with scales of justice" style="background:linear-gradient(135deg,#4e5560,#9a8e7e 55%,#2c2a28)"></div>
  <div class="card-shade"></div>
  <div class="card-label"><span>COMMERCIAL LITIGATION</span><span>&rarr;</span></div>
</div>
<div class="abs card" style="left:765px;top:1690px">
  <div class="card-photo" role="img" aria-label="Gavel resting on legal documents" style="background:linear-gradient(135deg,#d8d0c4,#8a5a36 55%,#3a2416)"></div>
  <div class="card-shade"></div>
  <div class="card-label"><span>BID DISPUTES</span><span>&rarr;</span></div>
</div>
<div class="abs btn-blue" style="left:476px;top:2054px;width:248px;height:46px">View More Practice Areas</div>

<!-- industries -->
<div class="abs eyebrow center" style="top:2288px;text-align:center">We Specialize In</div>
<h2 class="abs section-title center" style="top:2313px;text-align:center">Industries We Served</h2>

<div class="abs ind-card" style="left:140px;top:2381px">
  <svg width="70" height="70" viewBox="0 0 70 70" fill="none" stroke="#1877e0" stroke-width="2"><path d="M30 66V12M40 66V12M30 12h10M30 20l10 8M40 20l-10 8M30 36l10 8M40 36l-10 8M14 12h52M56 12v14M52 26h8v6h-8zM8 46h22v20H8zM8 56h22M19 46v20"/><path d="M4 66h62"/></svg>
  <h4>CONSTRUCTION</h4>
  <p>Ut wisi enim ad minim veniam, quis nostru ullamcorper suscipit lobortis nisl ut aliquip ex ea commodo.</p>
  <div class="arrow"><svg width="36" height="28" viewBox="0 0 36 28" fill="none" stroke="#1877e0" stroke-width="1.8"><path d="M26 6a12 12 0 1 0 0 16"/><path d="M10 14h24M28 8l6 6-6 6"/></svg></div>
</div>
<div class="abs ind-card" style="left:453px;top:2381px">
  <svg width="70" height="70" viewBox="0 0 70 70" fill="none" stroke="#1877e0" stroke-width="2"><rect x="14" y="6" width="42" height="54" rx="6"/><path d="M14 18h42M20 24h30v16H20zM20 50h6M44 50h6M18 60v6h8v-6M44 60v6h8v-6M8 26v10M62 26v10M28 12h14"/></svg>
  <h4>TRANSPORTATION</h4>
  <p>Ut wisi enim ad minim veniam, quis nostru ullamcorper suscipit lobortis nisl ut aliquip ex ea commodo.</p>
  <div class="arrow"><svg width="36" height="28" viewBox="0 0 36 28" fill="none" stroke="#1877e0" stroke-width="1.8"><path d="M26 6a12 12 0 1 0 0 16"/><path d="M10 14h24M28 8l6 6-6 6"/></svg></div>
</div>
<div class="abs ind-card" style="left:765px;top:2381px">
  <svg width="70" height="70" viewBox="0 0 70 70" fill="none" stroke="#1877e0" stroke-width="2"><path d="M10 8h50l6 16H4zM4 24c0 5 7 5 7 0 0 5 8 5 8 0 0 5 8 5 8 0 0 5 8 5 8 0 0 5 8 5 8 0 0 5 8 5 8 0 0 5 8 5 8 0M8 30v34h54V30M14 40h18v24H14zM38 40h18v14H38zM4 64h62M24 8v16M46 8v16"/></svg>
  <h4>RETAIL</h4>
  <p>Ut wisi enim ad minim veniam, quis nostru ullamcorper suscipit lobortis nisl ut aliquip ex ea commodo.</p>
  <div class="arrow"><svg width="36" height="28" viewBox="0 0 36 28" fill="none" stroke="#1877e0" stroke-width="1.8"><path d="M26 6a12 12 0 1 0 0 16"/><path d="M10 14h24M28 8l6 6-6 6"/></svg></div>
</div>

<!-- cta -->
<section class="abs cta" role="img" aria-label="Hands signing a contract on a dark wooden table"></section>
<div class="abs cta-shade"></div>
<h2 class="abs cta-title center" style="text-align:center">YOUR TRUSTED PARTNER IN<br>BUSINESS LITIGATION</h2>
<p class="abs cta-text" style="left:250px;width:700px;text-align:center">Ut wisi enim ad minim veniam, quis nostru ullamcorper suscipit lobortis nisl ut aliquip ex ea commodo conuat. Duis autem vel eum iriure dolor.</p>
<div class="abs btn-blue cta-btn">Contact Us Today</div>

<!-- blog -->
<div class="abs eyebrow center" style="top:3335px;text-align:center">Articles</div>
<h2 class="abs section-title center" style="top:3360px;text-align:center">Latest Blog Posts</h2>

<div class="abs blog-photo" role="img" aria-label="Three colleagues meeting around a laptop in an office"></div>
<div class="abs meta" style="left:140px;top:3742px">EXCEPTEUR SINT &nbsp; | &nbsp; Jan 2025</div>
<div class="abs post-title" style="left:140px;top:3773px">Ut Enim Ad Minim Veniam Quis Nostrud</div>
<p class="abs" style="left:140px;top:3806px;width:440px;font-size:12.5px;line-height:20px;color:var(--muted)">Excepteur sint occaecat cupidatat non proident, sunt in culpa qui officia deserunt mollit anim id est laborum.</p>
<div class="abs learn" style="left:140px;top:3859px">LEARN MORE &rarr;</div>

<div class="abs post-side" style="top:3442px"><div class="meta" style="font-size:12px">EXCEPTEUR SINT &nbsp;| &nbsp;Jan 2025</div><div class="post-title" style="margin-top:14px">Ut Enim Ad Mini Veiam<br>Quis Nostrud</div><div class="learn" style="margin-top:10px">LEARN MORE &rarr;</div></div>
<div class="abs thumb" style="top:3429px;background:linear-gradient(135deg,#5a4a3e,#a9957c 55%,#2d2520)" role="img" aria-label="Scales of justice and gavel on a desk"></div>
<div class="abs post-side" style="top:3596px"><div class="meta" style="font-size:12px">EXCEPTEUR SINT &nbsp;| &nbsp;Jan 2025</div><div class="post-title" style="margin-top:14px">Ut Enim Ad Mini Veiam<br>Quis Nostrud</div><div class="learn" style="margin-top:10px">LEARN MORE &rarr;</div></div>
<div class="abs thumb" style="top:3583px;background:linear-gradient(135deg,#d8d4cc,#9aa0a4 50%,#6a4a3a)" role="img" aria-label="Woman working on a laptop by a window"></div>
<div class="abs post-side" style="top:3750px"><div class="meta" style="font-size:12px">EXCEPTEUR SINT &nbsp;| &nbsp;Jan 2025</div><div class="post-title" style="margin-top:14px">Ut Enim Ad Mini Veiam<br>Quis Nostrud</div><div class="learn" style="margin-top:10px">LEARN MORE &rarr;</div></div>
<div class="abs thumb" style="top:3737px;background:linear-gradient(135deg,#3a3a40,#8a7a68 55%,#c8a070)" role="img" aria-label="Handshake beside a gavel"></div>

<div class="abs btn-blue" style="left:510px;top:3911px;width:180px;height:44px">View More Posts</div>

<!-- reviews -->
<section class="abs reviews"></section>
<div class="abs eyebrow" style="left:144px;top:4203px">Testimonials</div>
<h2 class="abs section-title" style="left:144px;top:4228px">Client Reviews</h2>
<p class="abs" style="left:144px;top:4273px;width:340px;font-size:12px;line-height:20px;color:var(--text)">Ut wisi enim ad minim venia quis nostr ullamcorper suscipit lobortis nisl ut aliquip ex ea coodo conuat. Duis autem vel eum iriure dolor in herit in vulputate velit esse molestie consegat vel illum.</p>
<div class="abs" style="left:144px;top:4373px;width:110px;height:32px">
  <div class="avatar" role="img" aria-label="Client portrait" style="left:0;background:#8b6b58"></div>
  <div class="avatar" role="img" aria-label="Client portrait" style="left:22px;background:#5e5048"></div>
  <div class="avatar" role="img" aria-label="Client portrait" style="left:44px;background:#9e8270"></div>
  <div class="avatar" role="img" aria-label="Client portrait" style="left:66px;background:#c4a48e"></div>
</div>
<div class="abs" style="left:144px;top:4420px;font-size:12.5px;color:var(--ink);display:flex;align-items:center;gap:8px"><svg width="14" height="14" viewBox="0 0 24 24"><path d="M12 2l3 7 7 .6-5.4 4.7 1.7 7.2L12 17.8 5.7 21.5l1.7-7.2L2 9.6 9 9z" fill="#f5b400"/></svg><span><b style="font-weight:600">5.0</b> (10k Reviews)</span></div>

<div class="abs quote-card-back"></div>
<div class="abs quote-card"></div>
<div class="abs quote-icon">&ldquo;</div>
<p class="abs" style="left:592px;top:4220px;width:408px;font-size:12px;line-height:24px;color:var(--text)">Ut wisi enim ad minim veniam, quis nostru ullamcorp suscipit lobortis nisl ut aliquip ex ea commodo conuat. Duis autem vel eum iriure dolor in henrrit in vuate velit esse motie consequat, vel illum dolore eu feugiat nulla faclisis at vero eros et accsan et iusto odio. Lorem ipsum dolor sit amet, consctetuer picing. Lorem ipsum dolor sit amet, consectetuer.</p>
<div class="abs" role="img" aria-label="Reviewer portrait" style="left:596px;top:4388px;width:50px;height:50px;border-radius:50%;background:#7a6458"></div>
<div class="abs" style="left:664px;top:4393px;font-size:13px;font-weight:700;color:var(--ink)">MARCUS T.</div>
<div class="abs" style="left:664px;top:4417px;font-size:12px;font-style:italic;color:var(--muted)">Lorem Ipsum</div>
<div class="abs slider-btn" style="left:541px;top:4319px;background:#9a9a9a"><svg width="8" height="10" viewBox="0 0 8 10"><path d="M6 1L2 5l4 4" stroke="#fff" stroke-width="1.6" fill="none"/></svg></div>
<div class="abs slider-btn" style="left:1024px;top:4319px;background:var(--blue)"><svg width="8" height="10" viewBox="0 0 8 10"><path d="M2 1l4 4-4 4" stroke="#fff" stroke-width="1.6" fill="none"/></svg></div>

<!-- footer -->
<footer class="abs footer"></footer>
<div class="abs foot-h" style="left:140px">QUICK LINKS</div>
<ul class="abs foot-list" style="left:140px;top:4678px">
  <li>Home</li><li>About Us</li><li>Professionals</li><li>Industries Served</li><li>Areas Of Practice</li><li>Resources &amp; Advisories</li>
</ul>
<div class="abs foot-h" style="left:382px">CONTACT DETAILS</div>
<div class="abs contact-item" style="left:382px;top:4682px;width:230px"><svg width="12" height="16" viewBox="0 0 12 16"><path d="M6 0a6 6 0 0 0-6 6c0 4.5 6 10 6 10s6-5.5 6-10a6 6 0 0 0-6-6zm0 8.5A2.5 2.5 0 1 1 6 3.5a2.5 2.5 0 0 1 0 5z" fill="#fff"/></svg><div><b>ADDRESS</b>123 Ut Wisi Enim Ad Minim<br>Veniam Quis Nostrud.</div></div>
<div class="abs contact-item" style="left:382px;top:4756px"><svg width="13" height="13" viewBox="0 0 24 24"><path d="M6.6 10.8a15 15 0 0 0 6.6 6.6l2.2-2.2c.3-.3.7-.4 1-.2 1.1.4 2.3.6 3.6.6.6 0 1 .4 1 1V20c0 .6-.4 1-1 1A17 17 0 0 1 3 4c0-.6.4-1 1-1h3.5c.6 0 1 .4 1 1 0 1.3.2 2.5.6 3.6.1.3 0 .7-.2 1z" fill="#fff"/></svg><div><b>PHONE</b>123-456-7890</div></div>
<div class="abs contact-item" style="left:382px;top:4809px"><svg width="13" height="11" viewBox="0 0 24 18"><path d="M0 0h24v18H0z" fill="#fff"/><path d="M1 1l11 9 11-9" stroke="#1877e0" stroke-width="2" fill="none"/></svg><div><b>EMAIL</b>info@haverlocktrialfirm.com</div></div>
<div class="abs foot-h" style="left:670px">FOLLOW US</div>
<div class="abs social" style="left:670px;top:4685px"><i></i>Linkfolk</div>
<div class="abs social" style="left:670px;top:4726px"><i></i>Vidcast</div>
<div class="abs social" style="left:670px;top:4767px"><i></i>Snapframe</div>
<div class="abs social" style="left:670px;top:4808px"><i></i>Chirpline</div>
<div class="abs foot-brand">HAVERLOCK<br><span style="font-size:18px;letter-spacing:4px">TRIAL FIRM</span></div>
<div class="abs copyright center" style="text-align:center">&copy; 2025 HAVERLOCK. All Rights Reserved.</div>

</body>
</html>
```